TALMORK

The business want a professional looking business card. We have a scetch we will add but want the extra upgrade, and would like more suggestions for variations of our business cards.

```html
<!DOCTYPE html>
<html lang="en">
<head>
<meta charset="utf-8">
<title>TALMORK – Business Card</title>
<link href="https://fonts.googleapis.com/css2?family=Cinzel:wght@600&family=Nunito+Sans:wght@300;400&display=swap" rel="stylesheet">
<style>
  :root {
    --bg: #e4e4e4;
    --gold-dark: #7a5632;
    --gold-mid: #a8894e;
    --gold-light: #efd681;
    --ink-light: #fbf6ea;
    --mark-gold: #e9c55c;
    --shadow: rgba(0, 0, 0, 0.18);
  }
  * { margin: 0; padding: 0; box-sizing: border-box; }
  html, body {
    width: 1200px;
    height: 745px;
    overflow: hidden;
    background: var(--bg);
  }
  .canvas {
    width: 1200px;
    height: 745px;
    display: flex;
    align-items: center;
    justify-content: center;
    gap: 44px;
  }
  .card {
    position: relative;
    width: 540px;
    height: 309px;
    border-radius: 3px;
    box-shadow: 0 14px 30px var(--shadow);
    overflow: hidden;
  }
  .card--front {
    background: linear-gradient(200deg, var(--gold-dark) 0%, var(--gold-mid) 55%, var(--gold-light) 100%);
    display: flex;
    align-items: center;
    justify-content: center;
  }
  .brand-lockup {
    display: flex;
    align-items: center;
    gap: 14px;
  }
  .brand-dot {
    width: 16px;
    height: 16px;
    border-radius: 50%;
    background: var(--mark-gold);
  }
  .brand-name {
    font-family: "Cinzel", serif;
    font-weight: 600;
    font-size: 40px;
    letter-spacing: 3px;
    color: var(--mark-gold);
  }
  .card--back {
    background: linear-gradient(20deg, var(--gold-dark) 0%, var(--gold-dark) 18%, var(--gold-mid) 60%, var(--gold-light) 100%);
    padding: 52px 46px 0 46px;
    color: var(--ink-light);
  }
  .holder-title {
    font-family: "Cinzel", serif;
    font-weight: 600;
    font-size: 27px;
    letter-spacing: 1.5px;
    line-height: 1;
  }
  .holder-role {
    font-family: "Nunito Sans", sans-serif;
    font-weight: 300;
    font-size: 24px;
    margin-top: 18px;
    padding-left: 22px;
    line-height: 1;
  }
  .holder-name {
    font-family: "Nunito Sans", sans-serif;
    font-weight: 300;
    font-size: 15px;
    margin-top: 6px;
    padding-left: 22px;
  }
  .contact-list {
    list-style: none;
    margin-top: 44px;
    padding-left: 52px;
    font-family: "Nunito Sans", sans-serif;
    font-weight: 300;
    font-size: 16px;
  }
  .contact-item {
    display: flex;
    align-items: center;
    gap: 12px;
    height: 24px;
  }
  .contact-icon {
    width: 15px;
    height: 15px;
    flex: none;
  }
</style>
</head>
<body>
<main class="canvas">
  <section class="card card--front" aria-label="Business card front">
    <div class="brand-lockup">
      <span class="brand-dot"></span>
      <span class="brand-name">TALMORK</span>
    </div>
  </section>

  <section class="card card--back" aria-label="Business card back">
    <h1 class="holder-title">TALMORK LUNDE</h1>
    <p class="holder-role">CEO &amp; Founder</p>
    <p class="holder-name">Erik Halvor Lunde</p>
    <ul class="contact-list">
      <li class="contact-item">
        <svg class="contact-icon" viewBox="0 0 16 16" fill="none" stroke="currentColor" stroke-width="1.4">
          <rect x="4" y="1" width="8" height="14" rx="1.5"/>
          <line x1="7" y1="12.5" x2="9" y2="12.5"/>
        </svg>
        <span>004790123456</span>
      </li>
      <li class="contact-item">
        <svg class="contact-icon" viewBox="0 0 16 16" fill="none" stroke="currentColor" stroke-width="1.4">
          <rect x="1" y="3.5" width="14" height="9"/>
          <polyline points="1,3.5 8,9 15,3.5"/>
        </svg>
        <span>talmork.llc@postvik.cm</span>
      </li>
      <li class="contact-item">
        <svg class="contact-icon" viewBox="0 0 16 16" fill="none" stroke="currentColor" stroke-width="1.2">
          <circle cx="8" cy="8" r="6.5"/>
          <ellipse cx="8" cy="8" rx="3" ry="6.5"/>
          <line x1="1.5" y1="8" x2="14.5" y2="8"/>
        </svg>
        <span>www.talmork.llc</span>
      </li>
    </ul>
  </section>
</main>
</body>
</html>
```